business card - Helicopter Flight Services, Flight School, etc.

We need a business card design for a new helicopter service.

We offer Helicopter Flight Services, Aerial Filming & Photography, Flight School, and Helicopter Tours. In that order.

Summit BladeAir, Inc.
Dennis Tollerby
SummitBladeair@Kestmail.com
626-418-7352

Based at the Brenwick Airport in Van Nuys, CA. The final design should communicate integrity and safety. Pictures or logos at your discretion.

Card back side - surprise me.

```html
<!DOCTYPE html>
<html lang="en">
<head>
<meta charset="utf-8">
<title>Summit BladeAir, Inc. — Business Card</title>
<link href="https://fonts.googleapis.com/css2?family=Bodoni+Moda:wght@500;700&family=Arimo:wght@400&display=swap" rel="stylesheet">
<style>
  :root {
    --page-bg: #ece9e4;
    --navy: #0b1148;
    --card-white: #ffffff;
    --ink: #111111;
    --rule: #3a3a3a;
    --sky-top: #c9c3d6;
    --sky-mid: #e6d6de;
    --ground: #c8cedd;
  }
  * { box-sizing: border-box; margin: 0; padding: 0; }
  html, body { width: 1200px; height: 902px; overflow: hidden; background: var(--page-bg); }
  .canvas {
    position: relative; width: 1200px; height: 902px;
    display: flex; align-items: center; justify-content: center; gap: 60px;
  }
  .card {
    position: relative; width: 530px; height: 303px; overflow: hidden;
    box-shadow: 0 6px 18px rgba(0,0,0,0.18);
  }
  /* Back side */
  .card-back {
    background: var(--navy); color: var(--card-white);
    display: flex; flex-direction: column; align-items: center; justify-content: center;
    text-align: center; padding: 0 20px;
  }
  .back-name {
    font-family: "Bodoni Moda", serif; font-weight: 700; font-size: 33px;
    letter-spacing: 1px; text-transform: uppercase; white-space: nowrap;
  }
  .back-tagline {
    font-family: "Bodoni Moda", serif; font-weight: 500; font-size: 15.5px;
    letter-spacing: 0.5px; margin-top: 8px; white-space: nowrap;
  }
  /* Front side */
  .card-front { background: var(--card-white); color: var(--ink); }
  .photo-area {
    position: absolute; inset: 0; opacity: 0.55;
    background: linear-gradient(180deg, var(--sky-top) 0%, var(--sky-mid) 45%, var(--ground) 70%, var(--ground) 100%);
  }
  .front-content {
    position: relative; height: 100%; padding: 26px 30px 0;
    display: flex; flex-direction: column; align-items: center; text-align: center;
  }
  .front-company {
    font-family: "Bodoni Moda", serif; font-weight: 700; font-size: 32px;
    text-transform: uppercase; letter-spacing: 1px; line-height: 1.15; white-space: nowrap;
  }
  .front-rule { width: 100%; height: 1px; background: var(--rule); margin: 6px 0 18px; }
  .holder-name {
    font-family: "Bodoni Moda", serif; font-weight: 700; font-size: 30px; margin-bottom: 20px;
    white-space: nowrap;
  }
  .contact-line { font-family: "Arimo", sans-serif; font-size: 18px; line-height: 1.6; white-space: nowrap; }
</style>
</head>
<body>
  <main class="canvas">
    <section class="card card-back">
      <p class="back-name">Summit BladeAir, Inc.</p>
      <p class="back-tagline">Flight Services · Aerial Filming · Flight School · Tours</p>
    </section>
    <section class="card card-front">
      <div class="photo-area" role="img" aria-label="Faded photo of a parked helicopter on an airfield at dusk"></div>
      <div class="front-content">
        <p class="front-company">Summit BladeAir, Inc.</p>
        <div class="front-rule"></div>
        <p class="holder-name">Dennis Tollerby</p>
        <p class="contact-line">626-418-7352</p>
        <p class="contact-line">SummitBladeair@Kestmail.com</p>
        <p class="contact-line">Brenwick Airport, Hangar 4 Ste.B&nbsp; Van Nuys, CA</p>
      </div>
    </section>
  </main>
</body>
</html>
```